Velmorique Shampoo

Velmorique shampoo is aimed to be a "novelty" item, with an intriguing mix of ingredients including but not limited to CBD & caffeine. We want a design that has a unique way of portraying "brainwash". Get creative with this one. We want the designers to get creative and think outside of the box, and maybe even get a little crazy (but not too crazy), because that's what the premise of the shampoo is; out of the box thinking -- "brainwash". Try to incorporate what you think of when you hear the word brainwash.

On the front of the bottle is where the main design will be shown. On the back will be the ingredients list, and will have a bit more information. The design should flow well with a darkish-brown bottle, pictured in the attachments called "bottle-size-template".

Avoid simple designs. We want our shampoo to stand out, not stand on the shelves. Get creative. IMPORTANT NOTE: Please do not use / inspire from the attachments called "bottle-size-template", as these are to show you what the bottle looks like, and what the label will look like on the bottle. DO NOT MAKE YOUR DESIGN BASED FROM THOSE ATTACHMENTS!

If you are feeling like a winner, you can even insert the correct ingredients list: Purified water (aqua), pure virgin hemp seed oil, green tea essential oil, green tea extract, aloe vera, ginseng extract, cam-phor essential oil, glycerin(vegetable), borage seed oil, lauryl glucoside, coconut oil, yucca extract, dermochlorella extract(seaweed based), nettle extract, coco glucoside, jojoba oil, awapuhi, soluble natural plant collagen, wheat germ glycerides (gluten free), echinacea extract, licorice root extract, cocoa butter, ivy extract, soy protein non-GMO), ascorbyl tetraisopalmitate (palm based), golden seal extract, behenic acid (natural based) guar gum, ylang ylang extract, sea salt.

```html
<!DOCTYPE html>
<html lang="en">
<head>
<meta charset="UTF-8">
<title>Velmorique Shampoo – Front Label</title>
<link rel="stylesheet" href="https://fonts.googleapis.com/css2?family=Bangers&family=Montserrat:ital,wght@0,500;0,700;1,500&display=swap">
<style>
  :root {
    --label-yellow: #e9c842;
    --label-yellow-light: #f1d85e;
    --burst-red: #e3253a;
    --burst-red-dark: #b3172a;
    --ink: #1c1a14;
    --paper: #fbf3ea;
    --brain-a: #e8413c;
    --brain-b: #3fc1d6;
    --brain-c: #7a3fb0;
    --brain-d: #f2a02a;
  }
  html, body {
    margin: 0;
    padding: 0;
    overflow: hidden;
  }
  .label {
    position: relative;
    width: 1200px;
    height: 1200px;
    overflow: hidden;
    background: radial-gradient(circle at 50% 30%, var(--label-yellow-light), var(--label-yellow) 70%);
    font-family: "Montserrat", sans-serif;
    color: var(--ink);
  }
  .tagline {
    position: absolute;
    top: 120px;
    width: 100%;
    text-align: center;
    font-size: 36px;
    font-weight: 500;
    letter-spacing: 1px;
    margin: 0;
  }
  .net-weight {
    position: absolute;
    top: 178px;
    width: 100%;
    text-align: center;
    font-size: 24px;
    font-weight: 700;
    margin: 0;
  }
  .burst {
    position: absolute;
    left: 0;
    top: 0;
  }
  .brain-art {
    position: absolute;
    left: 235px;
    top: 420px;
    width: 730px;
    height: 360px;
    border-radius: 48% 52% 40% 44% / 60% 58% 42% 40%;
    background: linear-gradient(120deg, var(--brain-a), var(--brain-d) 30%, var(--brain-b) 60%, var(--brain-c));
    border: 10px solid var(--paper);
    box-sizing: border-box;
  }
  .product-name {
    position: absolute;
    top: 790px;
    width: 100%;
    text-align: center;
    margin: 0;
    font-family: "Bangers", sans-serif;
    font-size: 120px;
    font-weight: 400;
    letter-spacing: 4px;
    color: var(--paper);
    line-height: 1;
  }
  .goodness {
    position: absolute;
    top: 930px;
    width: 100%;
    text-align: center;
    margin: 0;
    font-size: 28px;
    font-style: italic;
    font-weight: 500;
    color: var(--paper);
  }
  .ingredients {
    position: absolute;
    top: 970px;
    width: 100%;
    text-align: center;
    margin: 0;
    font-family: "Bangers", sans-serif;
    font-size: 54px;
    font-weight: 400;
    line-height: 1.05;
    letter-spacing: 1px;
    color: var(--paper);
  }
</style>
</head>
<body>
  <main class="label">
    <p class="tagline">EXPERT CARE FOR YOUR HAIR</p>
    <p class="net-weight">NET WT. 100ML</p>

    <svg class="burst" width="1200" height="1200" viewBox="0 0 1200 1200" aria-hidden="true">
      <defs>
        <linearGradient id="burstFill" x1="0" y1="0" x2="0" y2="1">
          <stop offset="0" stop-color="var(--burst-red)"/>
          <stop offset="1" stop-color="var(--burst-red-dark)"/>
        </linearGradient>
      </defs>
      <polygon fill="url(#burstFill)"
        points="600,330 680,420 800,360 790,470 920,440 870,540 1010,580 900,650 1000,760 890,790 960,900 1060,940 930,1000 990,1110 840,1060 790,1150 700,1080 600,1140 510,1070 400,1150 360,1060 210,1110 270,1000 140,940 250,890 200,790 110,760 210,650 100,580 240,540 190,440 320,470 310,360 430,420 520,340"/>
    </svg>

    <div class="brain-art" role="img" aria-label="Colourful comic-style brain illustration made of swirling rainbow strands"></div>

    <h1 class="product-name">VELMORIQUE</h1>
    <p class="goodness">With the goodness of</p>
    <p class="ingredients">GREEN TEA EXTRACT,<br>ALOE VERA</p>
  </main>
</body>
</html>
```